Aerospace Center needs app design

We need a design that would be a creative and innovative look of a simple idea connecting air traffic control situations with sonification.
We would like to see designs that use the elements shown in the short video which are different pads, showing 4 different colors, connecting with a degree and feeling of urgency. The different pads will be movable over screen, similar as to a whiteboard where you can move things around. Each of those pads has 4 different elements that are shown:
- ATC Event (you can chose different setups)
- Select a status (you can chose between Information, Caution and Alert. Color needs to feel more alert from Information to Alert.
- Notes box (you can open the box and write additional text on it)
- Music (you can chose different files. on the right side you can see a small group of notes. When you hover over the notes, music will be played without pressing a play or stop button.
The second video is an overview of music archival program that is connected with the pads.
Look and feel
Each slider illustrates characteristics of the customer's brand and the style your logo design should communicate.

```html
<!DOCTYPE html>
<html lang="en">
<head>
<meta charset="utf-8">
<title>Music Entries</title>
<link href="https://fonts.googleapis.com/css2?family=Inter:wght@400;500;600;700&display=swap" rel="stylesheet">
<style>
:root{
  --brand:#0c50b6;
  --brand-light:#4a90e8;
  --page:#e9ecf4;
  --white:#ffffff;
  --ink:#1b1f2a;
  --muted:#6b7282;
  --line:#dfe3ec;
  --field:#f3f4f8;
  --ok:#1fb85a;
  --warn:#f2c200;
  --alert:#e8141b;
}
*{box-sizing:border-box;margin:0;padding:0}
html,body{width:1114px;height:1200px;overflow:hidden;background:var(--white)}
body{font-family:"Inter",sans-serif;color:var(--ink);position:relative}
.abs{position:absolute}

/* sidebar */
.sidebar{position:absolute;background:var(--brand);width:45px}
.sidebar .brand{position:absolute;left:0;width:45px;text-align:center;color:var(--white);font-weight:600;font-size:8.5px}
.brand .mark{display:block;width:11px;height:11px;background:var(--white);margin:0 auto 4px;border-radius:2px}
.nav-icon{position:absolute;left:11px;width:22px;height:22px;color:var(--white)}
.nav-icon svg{width:22px;height:22px}
.active-pointer{position:absolute;right:0;width:0;height:0;border-top:5px solid transparent;border-bottom:5px solid transparent;border-right:5px solid var(--white)}
.nav-label{position:absolute;left:43px;color:var(--white);font-size:10px;font-weight:600;line-height:22px;white-space:nowrap}

/* top bar */
.topbar{position:absolute;left:45px;top:0;width:1069px;height:45px;background:var(--white)}
.round-btn{position:absolute;width:28px;height:28px;border-radius:50%;background:var(--field);display:flex;align-items:center;justify-content:center;color:#2f3545}
.round-btn svg{width:13px;height:13px}
.page-title{position:absolute;left:50px;top:12px;font-size:13px;font-weight:600}
.search{position:absolute;left:165px;top:8px;width:615px;height:27px;background:var(--field);border-radius:3px;display:flex;align-items:center;padding-left:11px;font-size:7px;color:var(--muted);gap:8px}
.search svg{width:10px;height:10px;color:#2f3545}
.avatar{position:absolute;left:934px;top:8px;width:28px;height:28px;border-radius:50%;background:linear-gradient(135deg,#c79a7a,#5b4030)}
.user{position:absolute;left:969px;top:11px;font-size:7.5px;line-height:10px}
.user .role{color:var(--brand-light)}
.user .name{font-weight:600}

/* content */
.content{position:absolute;left:45px;top:45px;width:1069px;height:461px;background:var(--page)}

.grid{display:grid;grid-template-columns:32px 28px 55px 64px 67px 65px 50px 53px 66px 35px 72px 50px 106px 106px 91px 96px;align-items:center}
.table-head{position:absolute;left:65px;top:71px;width:1036px;height:79px;background:var(--white);border:1px solid var(--line)}
.head-row{height:41px;border-bottom:1px solid var(--line);font-size:7.5px;font-weight:600;text-align:center;text-transform:uppercase}
.filter-row{height:37px}
.filter-row>div{height:37px;border-right:1px solid var(--line);display:flex;align-items:center;justify-content:center}
.filter-row>div:last-child{border-right:0}
.field{width:86%;height:16px;border:1px solid #cfd4de;background:var(--white);font-size:7px;color:var(--muted);display:flex;align-items:center;padding-left:6px}
.field.num{justify-content:center;padding-left:0}

.entry{position:absolute;left:65px;width:1036px;height:44px;background:var(--white);border:1px solid var(--line);font-size:8.5px;text-align:center}
.entry.landing{box-shadow:inset 4px 0 0 var(--ok)}
.entry.caution{box-shadow:inset 4px 0 0 var(--warn)}
.entry.alert{box-shadow:inset 4px 0 0 var(--alert)}
.entry .name{text-align:left;padding-left:4px}
.check{width:10px;height:10px;border:1px solid #9aa0ad;margin-left:12px;background:var(--white)}
.evt-landing{color:var(--ok)}
.evt-caution{color:var(--warn)}
.evt-alert{color:var(--alert)}
.player{display:block;width:63px;height:14px;margin:0 auto}
.notation{width:63px;height:31px;margin:0 auto;border-radius:3px;background:linear-gradient(90deg,#d4d6dc,#eceef2)}
.sets{font-size:7.5px;line-height:11px}
.note-box{width:81px;height:16px;border:1px solid #cfd4de;margin-left:9px}

/* lower section */
.section-title{position:absolute;left:93px;top:572px;font-size:16px;font-weight:700}
.tooltip{position:absolute;left:277px;top:731px;width:71px;height:20px;background:var(--brand-light);color:var(--white);font-size:7.5px;font-weight:500;display:flex;align-items:center;justify-content:center}
.tooltip::before{content:"";position:absolute;left:-4px;top:6px;border-top:4px solid transparent;border-bottom:4px solid transparent;border-right:4px solid var(--brand-light)}
</style>
</head>
<body>

<svg width="0" height="0" style="position:absolute">
  <defs>
    <symbol id="i-music" viewBox="0 0 24 24" fill="none" stroke="currentColor" stroke-width="1.6" stroke-linecap="round">
      <circle cx="5" cy="17" r="2.6"/><path d="M7.6 17V4.5l4-1.5V7"/><circle cx="17.5" cy="19" r="2.6"/><path d="M20.1 19V9h-7v10"/><path d="M13 12h7"/>
    </symbol>
    <symbol id="i-sliders" viewBox="0 0 24 24" fill="none" stroke="currentColor" stroke-width="1.6" stroke-linecap="round">
      <path d="M5 2v20M12 2v20M19 2v20"/><circle cx="5" cy="8" r="2.2" fill="var(--brand)"/><circle cx="12" cy="16" r="2.2" fill="var(--brand)"/><circle cx="19" cy="10" r="2.2" fill="var(--brand)"/>
    </symbol>
    <symbol id="i-event" viewBox="0 0 24 24" fill="none" stroke="currentColor" stroke-width="1.4" stroke-linecap="round">
      <path d="M12 2l1 2.2 2.3.2-1.8 1.5.6 2.3-2.1-1.3-2.1 1.3.6-2.3-1.8-1.5 2.3-.2z"/>
      <circle cx="5" cy="9" r="1.6"/><circle cx="19" cy="9" r="1.6"/><circle cx="12" cy="11" r="1.6"/>
      <path d="M2.5 22v-8h5v8M16.5 22v-8h5v8M9 22v-7.5h6V22M1 22h22"/>
    </symbol>
    <symbol id="i-chat" viewBox="0 0 24 24" fill="none" stroke="currentColor" stroke-width="1.5" stroke-linejoin="round" stroke-linecap="round">
      <path d="M8 4h14v10h-3v3l-3-3H8z"/><path d="M5 9H2v9h3v3l3-3h7v-2"/><path d="M11 7.5h8M11 10.5h8"/>
    </symbol>
    <symbol id="i-logout" viewBox="0 0 24 24" fill="none" stroke="currentColor" stroke-width="1.6" stroke-linejoin="round" stroke-linecap="round">
      <path d="M15 8V3H4v16l7 3V7L4 3"/><path d="M15 16v3h-4"/><path d="M14 12h8M19 9l3 3-3 3"/>
    </symbol>
    <symbol id="i-player" viewBox="0 0 63 14">
      <rect width="63" height="14" rx="7" fill="var(--brand)"/>
      <path d="M7 4.5v5l4-2.5z" fill="#fff"/>
      <path d="M15 7h32" stroke="#fff" stroke-width="1.6"/><circle cx="19" cy="7" r="2.2" fill="#fff"/>
      <path d="M51 5.5h2l2-2v7l-2-2h-2z" fill="#fff"/><path d="M57 5c1 1 1 3 0 4" stroke="#fff" stroke-width=".9" fill="none"/>
    </symbol>
  </defs>
</svg>

<!-- app -->
<aside class="sidebar" style="left:0;top:0;height:506px">
  <div class="brand" style="top:9px"><span class="mark"></span>SONA</div>
  <span class="nav-icon" style="top:101px"><svg><use href="#i-music"/></svg></span>
  <span class="active-pointer" style="top:107px"></span>
  <span class="nav-icon" style="top:148px"><svg><use href="#i-sliders"/></svg></span>
  <span class="nav-icon" style="top:189px"><svg><use href="#i-event"/></svg></span>
  <span class="nav-icon" style="top:231px"><svg><use href="#i-chat"/></svg></span>
  <span class="nav-icon" style="top:462px"><svg><use href="#i-logout"/></svg></span>
</aside>

<header class="topbar">
  <span class="round-btn" style="left:7px;top:8px"><svg viewBox="0 0 24 24" fill="none" stroke="currentColor" stroke-width="2" stroke-linecap="round"><path d="M4 6h16M4 12h16M4 18h16"/></svg></span>
  <h1 class="page-title">Music Entries</h1>
  <div class="search"><svg viewBox="0 0 24 24" fill="none" stroke="currentColor" stroke-width="2.4"><circle cx="11" cy="11" r="7"/><path d="M16 16l5 5"/></svg>Type your text here...</div>
  <span class="round-btn" style="left:857px;top:8px"><svg viewBox="0 0 24 24" fill="none" stroke="currentColor" stroke-width="1.8"><rect x="3" y="5" width="18" height="14" rx="3"/><path d="M3 8l9 6 9-6"/></svg></span>
  <span class="round-btn" style="left:893px;top:8px"><svg viewBox="0 0 24 24" fill="none" stroke="currentColor" stroke-width="1.8"><path d="M6 17V11a6 6 0 0 1 9-5.2M18 11v6M4 17h16M10 20h4"/><circle cx="18" cy="6" r="3" fill="var(--brand)" stroke="none"/></svg></span>
  <div class="avatar" role="img" aria-label="User profile photo"></div>
  <div class="user"><div class="role">Admin</div><div class="name">Lena Hart</div></div>
  <span class="round-btn" style="left:1035px;top:8px"><svg viewBox="0 0 24 24" fill="none" stroke="currentColor" stroke-width="1.8"><circle cx="12" cy="12" r="3.5"/><path d="M12 2.5l2 2.3 3-.6.9 2.9 2.9.9-.6 3 2.3 2-2.3 2 .6 3-2.9.9-.9 2.9-3-.6-2 2.3-2-2.3-3 .6-.9-2.9-2.9-.9.6-3L1.5 12l2.3-2-.6-3 2.9-.9.9-2.9 3 .6z"/></svg></span>
</header>

<main class="content"></main>

<section class="table-head">
  <div class="grid head-row">
    <div>Get</div><div>ID</div><div>Date</div><div>Name</div>
    <div style="grid-column:span 2">Orchestration Register</div>
    <div>Tempo</div><div>Dynamic</div><div>Complexity</div><div>Key</div><div>ATC Event</div><div>Priority</div><div>Sound File</div><div>Notation</div><div>Sets</div><div>Notes</div>
  </div>
  <div class="grid filter-row">
    <div></div><div></div><div></div>
    <div><span class="field">Nord</span></div>
    <div><span class="field">Piano</span></div>
    <div><span class="field">Deep</span></div>
    <div><span class="field num">150</span></div>
    <div><span class="field num">mf</span></div>
    <div><span class="field num">1</span></div>
    <div><span class="field num">c</span></div>
    <div><span class="field">Landing</span></div>
    <div><span class="field">0</span></div>
    <div></div><div></div><div></div>
    <div><span class="field"></span></div>
  </div>
</section>

<div class="entry grid landing" style="top:158px">
  <span class="check"></span><div>01</div><div>2021-09-03</div><div class="name">Nord Tocatta</div><div>Piano</div><div>Deep</div><div>150</div><div>mf</div><div>1</div><div>c</div><div class="evt-landing">Landing</div><div>0</div>
  <div><svg class="player"><use href="#i-player"/></svg></div><div class="notation" role="img" aria-label="Music notation snippet"></div><div class="sets">Famous Classical<br>Motifs</div><span class="note-box"></span>
</div>
<div class="entry grid caution" style="top:209px">
  <span class="check"></span><div>02</div><div>2021-09-03</div><div class="name">Nord Tocatta</div><div>Piano</div><div>Deep</div><div>150</div><div>mf</div><div>1</div><div>c</div><div class="evt-caution">Caution</div><div>0</div>
  <div><svg class="player"><use href="#i-player"/></svg></div><div class="notation" role="img" aria-label="Music notation snippet"></div><div class="sets">Famous Classical<br>Motifs</div><span class="note-box"></span>
</div>
<div class="entry grid" style="top:261px">
  <span class="check"></span><div>03</div><div>2021-09-03</div><div class="name">Nord Tocatta</div><div>Piano</div><div>Deep</div><div>150</div><div>mf</div><div>1</div><div>c</div><div></div><div>0</div>
  <div><svg class="player"><use href="#i-player"/></svg></div><div class="notation" role="img" aria-label="Music notation snippet"></div><div class="sets">Famous Classical<br>Motifs</div><span class="note-box"></span>
</div>
<div class="entry grid alert" style="top:314px">
  <span class="check"></span><div>04</div><div>2021-09-03</div><div class="name">Nord Tocatta</div><div>Piano</div><div>Deep</div><div>150</div><div>mf</div><div>1</div><div>c</div><div class="evt-alert">Alert</div><div>0</div>
  <div><svg class="player"><use href="#i-player"/></svg></div><div class="notation" role="img" aria-label="Music notation snippet"></div><div class="sets">Famous Classical<br>Motifs</div><span class="note-box"></span>
</div>
<div class="entry grid" style="top:367px">
  <span class="check"></span><div>05</div><div>2021-09-03</div><div class="name">Nord Tocatta</div><div>Piano</div><div>Deep</div><div>150</div><div>mf</div><div>1</div><div>c</div><div></div><div>0</div>
  <div><svg class="player"><use href="#i-player"/></svg></div><div class="notation" role="img" aria-label="Music notation snippet"></div><div class="sets">Famous Classical<br>Motifs</div><span class="note-box"></span>
</div>

<!-- menu states -->
<h2 class="section-title">MENU HOVER FUNCTION</h2>

<aside class="sidebar" style="left:96px;top:625px;height:509px">
  <div class="brand" style="top:10px"><span class="mark"></span>SONA</div>
  <span class="nav-icon" style="top:104px"><svg><use href="#i-music"/></svg></span>
  <span class="active-pointer" style="top:110px"></span>
  <span class="nav-icon" style="top:150px"><svg><use href="#i-sliders"/></svg></span>
  <span class="nav-icon" style="top:192px"><svg><use href="#i-event"/></svg></span>
  <span class="nav-icon" style="top:233px"><svg><use href="#i-chat"/></svg></span>
  <span class="nav-icon" style="top:464px"><svg><use href="#i-logout"/></svg></span>
</aside>

<aside class="sidebar" style="left:237px;top:625px;height:509px">
  <div class="brand" style="top:10px"><span class="mark"></span>SONA</div>
  <span class="nav-icon" style="top:104px"><svg><use href="#i-music"/></svg></span>
  <span class="nav-icon" style="top:150px"><svg><use href="#i-sliders"/></svg></span>
  <span class="nav-icon" style="top:192px"><svg><use href="#i-event"/></svg></span>
  <span class="nav-icon" style="top:233px"><svg><use href="#i-chat"/></svg></span>
  <span class="nav-icon" style="top:464px"><svg><use href="#i-logout"/></svg></span>
</aside>
<div class="tooltip">Music Entries</div>

<aside class="sidebar" style="left:368px;top:625px;height:509px;width:122px">
  <div class="brand" style="top:10px"><span class="mark"></span>SONA</div>
  <span class="nav-icon" style="top:104px"><svg><use href="#i-music"/></svg></span>
  <span class="nav-label" style="top:104px">Music Entries</span>
  <span class="nav-icon" style="top:150px"><svg><use href="#i-sliders"/></svg></span>
  <span class="nav-label" style="top:150px">Music Sets</span>
  <span class="nav-icon" style="top:192px"><svg><use href="#i-event"/></svg></span>
  <span class="nav-label" style="top:192px">ATC Events</span>
  <span class="nav-icon" style="top:233px"><svg><use href="#i-chat"/></svg></span>
  <span class="nav-label" style="top:233px">Help</span>
  <span class="nav-icon" style="top:464px"><svg><use href="#i-logout"/></svg></span>
  <span class="nav-label" style="top:464px">Logout</span>
</aside>

</body>
</html>
```